Brell Stone Company Business Cards

Front and Back Business Card - logo and text setup - cool design. I need workable photoshop or illustrator files so I can setup each employee card with design that is created
Updates

Hi everyone, thank you for the great entries. Please no more white and blue cards - there are so many already - black and silver only now please. thanks!

Target Market(s)

Construction Industry - Facility Managers

Industry/Entity Type

Construction

Contact Information for Business Card

I really like contemporary simplistic looks - clean neat....not opposed to seeing some black backrounds

Requirements
Must have
• Logo/website address with design on front only - www.brellstone-example.com (logo attached)
• Back:
• Name/Title/Company Address/Phone/email address
Nice to have
• Cool design
Should not have
• Nothing gimmicky like Fire or Water - since we are a Fire Protection company - it has all been done

```html
<!DOCTYPE html>
<html lang="en">
<head>
<meta charset="utf-8">
<title>Brell Stone Company Business Cards</title>
<link href="https://fonts.googleapis.com/css2?family=Lato:wght@400;900&display=swap" rel="stylesheet">
<style>
:root{
  --bg:#d4d4d4;
  --black:#161616;
  --ink:#232323;
  --silver:#b9bcc0;
  --silver-bright:#dcdee1;
  --text-light:#f1f1f1;
}
*{margin:0;padding:0;box-sizing:border-box}
html,body{width:1200px;height:1200px;overflow:hidden;background:var(--bg);font-family:'Lato',sans-serif}
.card{position:absolute;left:250px;width:708px;height:404px;box-shadow:0 6px 18px rgba(0,0,0,.3)}
.card-front{top:144px;background:var(--black)}
.card-back{top:582px;background:var(--ink)}
.wordmark{position:absolute;display:flex;align-items:center;gap:14px;font-weight:900;white-space:nowrap;letter-spacing:-.5px}
.wordmark .mark{display:block;background:var(--silver)}
.front-wordmark{left:0;right:0;top:164px;justify-content:center;font-size:58px;line-height:70px;color:var(--silver-bright)}
.front-wordmark .mark{width:26px;height:26px}
.front-url{position:absolute;left:0;right:0;top:344px;text-align:center;font-size:21px;color:var(--text-light)}
.accent{color:var(--silver)}
.back-wordmark{left:56px;top:170px;font-size:40px;color:var(--silver)}
.back-wordmark .mark{width:18px;height:18px}
.divider{position:absolute;left:381px;top:110px;width:2px;height:186px;background:var(--silver)}
.details{position:absolute;left:408px;top:104px;color:var(--text-light);font-size:16.5px;line-height:1.25}
.person-name{font-size:22px;color:var(--silver)}
.person-name .surname{color:var(--white,#fff)}
.person-title{margin-top:0}
.address{margin-top:14px}
.contacts{list-style:none;margin-top:9px}
.contacts li{display:flex;align-items:center;gap:8px;height:21.5px}
.contacts svg{width:13px;height:13px;fill:var(--silver);flex:none}
</style>
</head>
<body>
<section class="card card-front">
  <div class="wordmark front-wordmark"><span class="mark"></span>Brell Stone</div>
  <p class="front-url">www.<span class="accent">brellstone-example</span>.com</p>
</section>

<section class="card card-back">
  <div class="wordmark back-wordmark"><span class="mark"></span>Brell Stone</div>
  <div class="divider"></div>
  <div class="details">
    <p class="person-name">Dana <span class="surname">Merrow</span></p>
    <p class="person-title">Director</p>
    <p class="address">48 Harbor Point Road<br>Lakeview, NY 10000</p>
    <ul class="contacts">
      <li><svg viewBox="0 0 16 16"><path d="M3 1l3 3-1.5 2c1 2 3 4 5 5L11.5 9.5l3 3-2 2.5C6.5 15 1 9.5 1 3z"/></svg><span>(555) 010-2841</span></li>
      <li><svg viewBox="0 0 16 16"><path d="M4 1h8v4H4zM1 6h14v6h-3v3H4v-3H1zM5 10v4h6v-4z"/></svg><span>(555) 010-2842</span></li>
      <li><svg viewBox="0 0 16 16"><path d="M1 3h14v1L8 9 1 4zM1 6l7 5 7-5v7H1z"/></svg><span>info@brellstone-example.com</span></li>
      <li><svg viewBox="0 0 16 16"><circle cx="8" cy="8" r="6.5" fill="none" stroke="#b9bcc0" stroke-width="1.3"/><path d="M1.5 8h13M8 1.5c-3 3.5-3 9.5 0 13M8 1.5c3 3.5 3 9.5 0 13" stroke="#b9bcc0" stroke-width="1.1" fill="none"/></svg><span>www.<span class="accent">brellstone-example</span>.com</span></li>
    </ul>
  </div>
</section>
</body>
</html>
```